Landing Page Design for Adult Dating Age Verification (18+)

The objective of this task is to design a visually appealing pre-landing page for the adult dating site "Quillmera (site: https://quillmera.com/)" with an age verification mechanism. The pre-landing page will feature two buttons that redirect visitors to the main offer. The design should also include a footer block that includes links to the terms of use, privacy policy, and contact us pages.

Design Requirements:
Develop an age verification section prominently displayed on the pre-landing page.
Design the section to include two buttons labeled "Yes" and "No" for visitors to confirm their age.
Ensure the section is visually appealing and clearly communicates the purpose of age verification.

Visual Appeal:
Create a visually appealing design that aligns with the branding and theme of the "Quillmera" adult dating site.
Use suitable color schemes, typography, and graphics to enhance the overall visual appeal of the pre-landing page.

Layout and Navigation:
Design an engaging and intuitive layout that encourages visitors to interact with the page and proceed to the main offer.
Ensure clear and visible navigation elements that direct visitors to the main offer or provide additional information.

Responsive Design:
Develop a responsive design that provides a seamless user experience across various devices, including desktop and mobile.
Ensure the design elements and layout adapt well to different screen sizes and resolutions.

File Formats and Assets:
Deliver the final design in PSD, AI, or Sketch format, ensuring that the files are well-organized and layered.
Include any necessary images or assets used in the design, ensuring they are of high quality and optimized for web use.

```html
<!DOCTYPE html>
<html lang="en">
<head>
<meta charset="utf-8">
<title>Quillmera – Age Verification</title>
<link rel="stylesheet" href="https://fonts.googleapis.com/css2?family=Figtree:wght@500;600;700&family=Playfair+Display:wght@700&display=swap">
<style>
  :root{
    --bg-deep:#0b0606;
    --bg-warm:#2a1c19;
    --bg-mid:#1a1110;
    --panel:rgba(58,44,44,0.72);
    --panel-border:#c02a6c;
    --accent:#ff2a8c;
    --text:#ffffff;
    --outline:#c8c8c8;
  }
  *{box-sizing:border-box;margin:0;padding:0}
  html,body{width:1200px;height:669px;overflow:hidden;background:var(--bg-deep)}
  body{font-family:"Figtree",sans-serif;color:var(--text);position:relative}
  .hero-photo{
    position:absolute;inset:0;
    background:
      radial-gradient(ellipse 45% 40% at 40% 35%, rgba(120,80,64,0.45), transparent 70%),
      radial-gradient(ellipse 40% 45% at 62% 55%, rgba(110,78,66,0.35), transparent 70%),
      radial-gradient(ellipse 60% 30% at 55% 88%, rgba(70,60,60,0.5), transparent 75%),
      linear-gradient(180deg,var(--bg-mid),var(--bg-deep));
  }
  .age-gate{
    position:absolute;left:414px;top:191px;width:372px;height:258px;
    border:1px solid var(--panel-border);border-radius:19px;
    background:var(--panel);text-align:center;
  }
  .brand{
    position:absolute;top:23px;left:0;right:0;
    display:flex;justify-content:center;align-items:center;gap:5px;
    font-size:11px;font-weight:700;letter-spacing:.2px;
  }
  .brand-dot{width:14px;height:14px;border-radius:50%;background:#d9a6dc}
  .gate-title{
    position:absolute;top:50px;left:0;right:0;
    font-size:29px;font-weight:700;letter-spacing:-.3px;
  }
  .gate-sub{position:absolute;top:96px;left:0;right:0;font-size:12.5px;font-weight:600}
  .btn{
    position:absolute;top:128px;height:35px;
    display:flex;align-items:center;justify-content:center;
    font-size:10.5px;font-weight:700;color:var(--text);text-decoration:none;
  }
  .btn-yes{left:47px;width:128px;background:var(--accent)}
  .btn-no{left:190px;width:135px;border:1px solid var(--outline)}
  .gate-legal{
    position:absolute;top:189px;left:45px;width:290px;text-align:left;
    font-size:12.2px;font-weight:600;line-height:19px;
  }
</style>
</head>
<body>
  <div class="hero-photo" role="img" aria-label="Dimly lit photo of a couple embracing on a bed"></div>
  <section class="age-gate">
    <div class="brand"><span class="brand-dot"></span><span>Quillmera</span></div>
    <h1 class="gate-title">Welcome to Quillmera</h1>
    <p class="gate-sub">Please, verify your age to enter</p>
    <a class="btn btn-yes" href="https://quillmera.com/">I AM OVER 18 YEARS</a>
    <a class="btn btn-no" href="https://quillmera.com/">I AM UNDER 18 YEARS</a>
    <p class="gate-legal">By entering this site you are agreeing to the Terms of Use and Privacy Policy.</p>
  </section>
</body>
</html>
```